Kestrel Facilities Business Card Design

We would now like to design business cards with the new Kestrel Facilities logo

Target Market(s)

Professional

Industry/Entity Type

Professional services

Contact Information for Business Card

Employee name, title, phone number, email address, corporate office address and logo.

Font styles to use
Sans Serif

Colors
0054AA
0677BA
7BADD7
CADEEF
E8F1F8

Requirements
Must have
• My logo
Should not have
• any other pictures or images besides my logo

```html
<!DOCTYPE html>
<html lang="en">
<head>
<meta charset="utf-8">
<title>Kestrel Facilities Business Card</title>
<link rel="stylesheet" href="https://fonts.googleapis.com/css2?family=Oswald:wght@500&family=Mulish:wght@400&family=Roboto:wght@400&display=swap">
<style>
  :root {
    --brand-blue: #0a84e6;
    --ink-grey: #555a60;
    --card-white: #ffffff;
    --backdrop: #e4e6e8;
  }
  * { margin: 0; padding: 0; box-sizing: border-box; }
  html, body {
    width: 1200px; height: 1200px; overflow: hidden;
    background: var(--backdrop);
  }
  .stage { position: relative; width: 1200px; height: 1200px; }
  .card {
    position: absolute; left: 257px; width: 686px; height: 392px;
    background: var(--card-white); overflow: hidden;
  }
  .card--front { top: 165px; }
  .card--back { top: 653px; }

  .contact { position: absolute; left: 47px; top: 82px; }
  .contact__name {
    font-family: "Oswald", sans-serif; font-weight: 500;
    font-size: 28px; line-height: 1; color: var(--brand-blue);
    letter-spacing: 0.2px; text-transform: uppercase;
  }
  .contact__title, .contact__address, .contact__line {
    font-family: "Mulish", sans-serif; font-weight: 400;
    font-size: 15px; color: var(--ink-grey);
  }
  .contact__title { margin-top: 3px; }
  .contact__address { margin-top: 24px; line-height: 19.5px; font-style: normal; }
  .contact__list { list-style: none; margin-top: 12px; }
  .contact__line { display: flex; align-items: center; height: 19.8px; }
  .contact__icon { width: 13px; height: 13px; margin-right: 9px; fill: var(--brand-blue); flex: none; }

  .front-brand {
    position: absolute; left: 292px; top: 0; width: 394px; height: 392px;
    display: flex; flex-direction: column; justify-content: center;
    align-items: flex-start; padding-left: 52px; gap: 18px;
  }
  .front-brand__square {
    width: 92px; height: 92px; background: var(--brand-blue);
  }
  .front-brand__name {
    font-family: "Oswald", sans-serif; font-weight: 500;
    font-size: 66px; line-height: 1.05; color: var(--brand-blue);
    text-transform: uppercase;
  }

  .brand-lockup {
    position: absolute; left: 0; right: 0; top: 94px;
    display: flex; align-items: center; justify-content: center; gap: 18px;
  }
  .brand-lockup__square {
    width: 180px; height: 180px; background: var(--brand-blue);
  }
  .brand-lockup__name {
    font-family: "Oswald", sans-serif; font-weight: 500;
    font-size: 44px; line-height: 1.1; color: var(--brand-blue);
    text-transform: uppercase;
  }
  .brand-web {
    position: absolute; left: 0; right: 0; top: 332px; text-align: center;
    font-family: "Roboto", sans-serif; font-size: 16px;
    letter-spacing: 5px; color: var(--ink-grey); text-transform: uppercase;
  }
</style>
</head>
<body>
<main class="stage">
  <section class="card card--front">
    <div class="contact">
      <h1 class="contact__name">Daniel Hart</h1>
      <p class="contact__title">President</p>
      <address class="contact__address">4120 Alder Ridge Road<br>Fairbanks<br>Alaska 99709</address>
      <ul class="contact__list">
        <li class="contact__line">
          <svg class="contact__icon" viewBox="0 0 16 16" aria-hidden="true"><path d="M3.6 1.2l2.3 2.6-1.3 2a9 9 0 0 0 5.6 5.6l2-1.3 2.6 2.3-1.4 2.4C7.6 16 0 8.4 1.2 2.6z"/></svg>
          555-214-7730
        </li>
        <li class="contact__line">
          <svg class="contact__icon" viewBox="0 0 16 16" aria-hidden="true"><path d="M4 0h8a1 1 0 0 1 1 1v14a1 1 0 0 1-1 1H4a1 1 0 0 1-1-1V1a1 1 0 0 1 1-1zm1 2v10h6V2zm3 11a1 1 0 1 0 0 2 1 1 0 0 0 0-2z"/></svg>
          555-318-6042
        </li>
        <li class="contact__line">
          <svg class="contact__icon" viewBox="0 0 16 16" aria-hidden="true"><path d="M0 4h16v10H0zm1.5 1.5L8 10l6.5-4.5v-0.2H1.5z"/></svg>
          info@kestrelfacilities.com
        </li>
        <li class="contact__line">
          <svg class="contact__icon" viewBox="0 0 16 16" aria-hidden="true"><circle cx="8" cy="8" r="7.5"/></svg>
          www.kestrelfacilities.com
        </li>
      </ul>
    </div>
    <div class="front-brand">
      <div class="front-brand__square" aria-hidden="true"></div>
      <p class="front-brand__name">Kestrel<br>Facilities</p>
    </div>
  </section>

  <section class="card card--back">
    <div class="brand-lockup">
      <div class="brand-lockup__square" aria-hidden="true"></div>
      <p class="brand-lockup__name">Kestrel<br>Facilities</p>
    </div>
    <p class="brand-web">www.kestrelfacilities.com</p>
  </section>
</main>
</body>
</html>
```